Corvane Freight Company Business Card Design

We are a company that delivers natural saltwater (from the ocean) to aquarium companies, restaurants and home marine tanks. I would like a new business card to suit.

Must include Name, company name, abn, contact number and website as well as logo (see attached).

Looking for a design that stands out, has a clean but unique appearance.

Double and single sided entries welcome

Business

• Logo

```html
<!DOCTYPE html>
<html lang="en">
<head>
<meta charset="utf-8">
<title>Corvane Freight Company – Business Card</title>
<link rel="stylesheet" href="https://fonts.googleapis.com/css2?family=Source+Sans+3:wght@400;600;700&display=swap">
<style>
  :root {
    --backdrop: #1d1d1f;
    --card-blue: #1a6ff0;
    --card-blue-light: #4aa6f4;
    --corner-pale: #a9dcfb;
    --corner-mid: #55acf5;
    --text-white: #ffffff;
    --text-soft: #e3efff;
    --divider: #f08f7a;
  }
  * { margin: 0; padding: 0; box-sizing: border-box; }
  html, body {
    width: 1200px;
    height: 1085px;
    overflow: hidden;
    background: var(--backdrop);
    font-family: "Source Sans 3", "Myriad Pro", sans-serif;
    color: var(--text-white);
  }
  .canvas { position: relative; width: 1200px; height: 1085px; }
  .card {
    position: absolute;
    width: 762px;
    height: 435px;
    background: var(--card-blue);
    overflow: hidden;
  }
  .card--front { left: 65px; top: 75px; }
  .card--back { left: 353px; top: 572px; }

  .corner-art {
    position: absolute;
    right: 0;
    top: 0;
    width: 420px;
    height: 290px;
    background: radial-gradient(ellipse at 72% 30%, var(--corner-pale) 0%, var(--corner-mid) 45%, rgba(26, 111, 240, 0) 78%);
  }

  .holder { position: absolute; right: 36px; top: 22px; text-align: right; }
  .holder__name { font-weight: 700; font-size: 32px; line-height: 1.1; }
  .holder__title { font-weight: 400; font-size: 24px; line-height: 1.2; color: var(--text-soft); }

  .brand-name {
    position: absolute;
    font-weight: 700;
    color: var(--text-white);
    white-space: nowrap;
    display: flex;
    align-items: center;
    gap: 14px;
    transform: translate(-50%, -50%);
  }
  .brand-name__dot {
    width: 22px; height: 22px; border-radius: 50%;
    background: var(--card-blue-light);
    flex: none;
  }
  .card--front .brand-name { left: 255px; top: 165px; font-size: 50px; }
  .card--back .brand-name { left: 380px; top: 197px; font-size: 56px; }

  .contact { position: absolute; left: 40px; top: 308px; font-size: 18px; line-height: 29px; }
  .contact__row { display: flex; align-items: center; gap: 6px; }
  .contact__icon { width: 14px; height: 14px; flex: none; }

  .divider {
    position: absolute; left: 250px; top: 344px;
    width: 2px; height: 55px; background: var(--divider);
  }
  .company { position: absolute; left: 270px; top: 337px; font-size: 18px; line-height: 29px; }
  .company__name { font-weight: 700; }

  .web-line {
    position: absolute; left: 0; right: 0; top: 346px;
    text-align: center; font-size: 24px; letter-spacing: 4px;
    color: var(--text-soft);
  }
</style>
</head>
<body>
<main class="canvas">

  <section class="card card--front" aria-label="Business card front">
    <div class="corner-art" role="img" aria-label="Decorative light blue corner accent"></div>

    <div class="holder">
      <p class="holder__name">Your name</p>
      <p class="holder__title">Title</p>
    </div>

    <p class="brand-name"><span class="brand-name__dot"></span>Corvane Freight</p>

    <div class="contact">
      <p class="contact__row">
        <svg class="contact__icon" viewBox="0 0 14 14" aria-hidden="true">
          <circle cx="7" cy="7" r="6" fill="none" stroke="#fff" stroke-width="1.2"/>
          <path d="M4.5 3.8 L6 3.5 L6.5 5.5 L5.6 6.1 Q6.4 7.8 7.9 8.5 L8.5 7.6 L10.4 8.1 L10.2 9.6 Q6 10 4.5 3.8 Z" fill="#fff"/>
        </svg>
        123-456-7890
      </p>
      <p class="contact__row">
        <svg class="contact__icon" viewBox="0 0 14 14" aria-hidden="true">
          <circle cx="7" cy="7" r="6" fill="#fff"/>
          <path d="M1 7 H13 M7 1 Q3.5 7 7 13 M7 1 Q10.5 7 7 13" stroke="#1a6ff0" stroke-width="1" fill="none"/>
        </svg>
        www.website.com
      </p>
      <p class="contact__row">ABN : 0123456789</p>
    </div>

    <span class="divider" aria-hidden="true"></span>

    <div class="company">
      <p class="company__name">Corvane Freight Company</p>
      <p class="company__address">Street Name, City Name, State, City Zip Code</p>
    </div>
  </section>

  <section class="card card--back" aria-label="Business card back">
    <p class="brand-name"><span class="brand-name__dot"></span>Corvane Freight</p>
    <p class="web-line">www.website.com</p>
  </section>

</main>
</body>
</html>
```